Real estate broker business card

Want a modern celan but effective business card for my residential and commercial real estate business. I want the back of the card to advertise my services and to capture business. I have attached the back of my current business card fore ideas
Updates

Logos, photo and text updates added! Added Saturday, September 3, 2016

Project Deadline Extended Reason: LOGOS, PHOTOS AND TEST JUST UPLOADED! I'M READY TO PICK A DESIGN! THANK YOU! Added Saturday, September 3, 2016

Target Market(s)

home buyers and seller. commercial buyers and sellers

Industry/Entity Type

Real Estate

Contact Information for Business Card

must have my contact information and my photo

Requirements
Must have
• Carla Ventrino
• Owner & Qualifying Broker
• Ventrino Real Estate Services
• 505.718.2094
• carla@ventrinohomes.example
• www.ventrinohomes.example
Nice to have
• metallic
• Business capture text: " Don't buy or lease property without someone looking out for your best interests. I will represent you on your home or investment purchase for FREE!"
• "Home owners, call today to receive a FREE market analysis for your homes value!

```html
<!DOCTYPE html>
<html lang="en">
<head>
<meta charset="utf-8">
<title>Ventrino Real Estate Services – Business Card</title>
<link href="https://fonts.googleapis.com/css2?family=Cinzel:wght@700&family=Montserrat:wght@400;500;600&display=swap" rel="stylesheet">
<style>
  :root {
    --teal: #1a6f7c;
    --ink: #3a3d42;
    --grey-line: #6b6e73;
    --grey-band: #5f6266;
    --card-white: #ffffff;
    --card-grey: #e5e6e8;
    --backdrop: #2c2d30;
    --frame: #4a4c50;
  }
  * { box-sizing: border-box; margin: 0; padding: 0; }
  html, body {
    width: 1200px; height: 900px; overflow: hidden;
    background: var(--backdrop);
    font-family: "Montserrat", Arial, sans-serif;
  }
  .stage { position: relative; width: 1200px; height: 900px; }
  .card {
    position: absolute; left: 267px;
    width: 665px; height: 380px;
    border-radius: 22px; overflow: hidden;
  }
  /* ---------- back ---------- */
  .card-back {
    top: 50px; background: var(--card-grey);
    display: flex; flex-direction: column; align-items: center;
    text-align: center; padding-top: 62px;
  }
  .brand-mark {
    display: flex; align-items: center; gap: 10px;
    font-family: "Cinzel", Georgia, serif; font-weight: 700;
    color: var(--teal); white-space: nowrap;
  }
  .brand-mark .dot {
    flex: none; width: 16px; height: 16px; border-radius: 50%; background: var(--teal);
  }
  .card-back .brand-mark { font-size: 30px; margin-bottom: 38px; }
  .pitch {
    font-size: 17px; line-height: 1.32; color: var(--ink);
    max-width: 440px; margin-bottom: 16px;
  }
  .pitch strong { color: var(--teal); font-weight: 600; }
  /* ---------- front ---------- */
  .card-front { top: 470px; background: var(--card-white); }
  .card-front .decor { position: absolute; inset: 0; }
  .card-front .brand-mark {
    position: absolute; left: 40px; top: 150px;
    font-size: 19px; gap: 12px;
  }
  .card-front .brand-mark .dot { width: 36px; height: 36px; }
  .portrait {
    position: absolute; left: 445px; top: 26px;
    width: 182px; height: 160px;
    border: 4px solid var(--frame);
    background: linear-gradient(135deg, #3e5a2c 0%, #2f4420 45%, #6b4a3a 70%, #d9c9bd 100%);
  }
  .identity {
    position: absolute; right: 38px; top: 196px; text-align: right;
  }
  .identity .name {
    font-family: "Cinzel", Georgia, serif; font-weight: 700;
    font-size: 24px; color: var(--teal); letter-spacing: 0.5px;
    padding-bottom: 4px; border-bottom: 1.5px solid var(--grey-line);
  }
  .identity .title { font-size: 15px; color: var(--ink); margin-top: 4px; }
  .contacts {
    position: absolute; left: 42px; top: 280px;
    list-style: none; font-size: 16px; color: var(--ink);
  }
  .contacts li { display: flex; align-items: center; gap: 12px; height: 24px; }
  .contacts svg { width: 13px; height: 13px; fill: var(--teal); }
</style>
</head>
<body>
<main class="stage">

  <section class="card card-back" aria-label="Card back">
    <div class="brand-mark"><span class="dot"></span>Ventrino</div>
    <p class="pitch">Don't buy or lease property without someone looking out for your best interests. I will represent you on your home or investment purchase for <strong>FREE</strong>!</p>
    <p class="pitch">Home owners, call today to receive a <strong>FREE</strong> market analysis for your homes value!</p>
  </section>

  <section class="card card-front" aria-label="Card front">
    <svg class="decor" viewBox="0 0 665 380" aria-hidden="true">
      <line x1="36" y1="268" x2="470" y2="268" stroke="#6b6e73" stroke-width="1.5"/>
      <polygon points="456,380 490,262 665,262 665,380" fill="#5f6266"/>
      <polygon points="472,380 504,272 665,272 665,380" fill="#1a6f7c"/>
    </svg>

    <div class="brand-mark"><span class="dot"></span>Ventrino Real Estate Services</div>

    <div class="portrait" role="img" aria-label="Portrait photo of Carla Ventrino"></div>

    <div class="identity">
      <div class="name">CARLA VENTRINO</div>
      <div class="title">Owner &amp; Qualifying Broker</div>
    </div>

    <ul class="contacts">
      <li><svg viewBox="0 0 16 16"><path d="M3.6 1.2l2.3 2.7-1.3 1.9c.9 2 2.6 3.7 4.6 4.6l1.9-1.3 2.7 2.3-1.3 2.4C7 13.6 2.4 9 1.2 3.1z"/></svg>505.718.2094</li>
      <li><svg viewBox="0 0 16 16"><path d="M1 3h14v10H1zM2.5 4.5v.3L8 8.6l5.5-3.8v-.3zM2.5 6.6v4.9h11V6.6L8 10.4z"/></svg>carla@ventrinohomes.example</li>
      <li><svg viewBox="0 0 16 16"><circle cx="8" cy="8" r="7"/></svg>www.ventrinohomes.example</li>
    </ul>
  </section>

</main>
</body>
</html>
```